Fun conversation piece for the home depicting the history of the ownership (title) and more!

We need some ideas for a framed display to be hung in a home for a new company I started called Tale of Dwelling, LLC. We will create framed (or unframed canvass) wall displays depicting the Tale of the Dwelling (title transfers) with some interesting background on the subdivision the home is located. This will be a conversation piece. Use color if you feel that works best. I am envisioning perhaps the writing to be in old English or old Spanish font to reflect the history of Florida where I am located. I am wanting to incorporate perhaps a picture of the home converted into sketch as a background to the "history". Or we could skip that and use the vegetation (trees) native to the area for a background. I am going to attach something I found online as a sample but I am open to ideas. The sample is a little formal for what I am trying to do. I may sell these framed or as unframed canvass pictures which might need to be a bit more contemporary. I also need a logo if you have any ideas. TD in some form of old English style perhaps? The document attached labeled "Wrenmarsh" is an example of the content I will be creating for the picture.
Updates

I misspelled "States" in one of the paragraphs. Can you correct that for me? United States. Not "sates". My bad.

Logo Text

Tale of Dwelling (or TD). Surprise me.

```html
<!DOCTYPE html>
<html lang="en">
<head>
<meta charset="utf-8">
<title>Wrenmarsh – Tale of Dwelling</title>
<link href="https://fonts.googleapis.com/css2?family=Almendra+SC&family=Almendra+Display&family=Josefin+Sans:wght@400&display=swap" rel="stylesheet">
<style>
  :root {
    --ink: #050505;
    --cream: #f1e4c4;
    --cream-soft: rgba(241, 228, 196, 0.16);
    --umber: #6e5638;
    --umber-deep: #4a3a25;
  }
  * { margin: 0; padding: 0; box-sizing: border-box; }
  html, body { width: 848px; height: 1200px; overflow: hidden; background: var(--ink); }
  .poster {
    position: relative; width: 848px; height: 1200px; overflow: hidden;
    background: var(--ink); color: var(--cream);
    font-family: "Almendra SC", serif;
  }
  .backdrop-trees {
    position: absolute; left: 0; top: 180px; width: 848px; height: 1020px;
    background:
      radial-gradient(ellipse 260px 380px at 230px 360px, rgba(110, 86, 56, 0.85), transparent 70%),
      radial-gradient(ellipse 220px 260px at 520px 560px, rgba(110, 86, 56, 0.55), transparent 70%),
      radial-gradient(ellipse 500px 180px at 420px 950px, rgba(110, 86, 56, 0.8), transparent 70%),
      radial-gradient(ellipse 200px 300px at 80px 700px, rgba(74, 58, 37, 0.7), transparent 70%);
  }
  .frame { position: absolute; inset: 0; }
  .ornament {
    position: absolute; background: var(--cream-soft); border-radius: 50%;
  }
  .ornament.corner { width: 120px; height: 120px; }
  .ornament.top-left { left: 30px; top: 30px; }
  .ornament.top-right { right: 30px; top: 30px; }
  .ornament.bottom-left { left: 30px; bottom: 30px; }
  .ornament.bottom-right { right: 30px; bottom: 30px; }
  .ornament.crest-top { left: 250px; top: 108px; width: 348px; height: 50px; border-radius: 40px; }
  .ornament.crest-bottom { left: 250px; top: 334px; width: 348px; height: 42px; border-radius: 40px; }
  .label-tab {
    position: absolute; left: 330px; top: 74px; width: 188px; height: 28px;
    font-family: "Josefin Sans", sans-serif; font-size: 17px; text-align: center; line-height: 30px;
  }
  .title {
    position: absolute; left: 165px; top: 190px; width: 518px; text-align: center;
    font-family: "Almendra Display", serif; font-size: 82px; line-height: 100px;
    letter-spacing: 1px; color: var(--cream);
    text-shadow: 3px 3px 0 var(--umber-deep);
  }
  .years {
    position: absolute; left: 0; top: 382px; width: 848px; text-align: center;
    font-family: "Josefin Sans", sans-serif; font-size: 20px; letter-spacing: 1px;
  }
  .history {
    position: absolute; left: 110px; top: 448px; width: 628px; text-align: center;
    font-size: 11.6px; line-height: 19.6px; text-align-last: center;
  }
  .history p { text-align: justify; text-align-last: center; }
  .ledger-heading {
    position: absolute; left: 0; top: 836px; width: 848px; text-align: center; font-size: 12px;
  }
  .ledger {
    position: absolute; left: 118px; top: 878px; width: 620px; border-collapse: collapse; font-size: 12px;
  }
  .ledger td { height: 22px; padding: 0; }
  .ledger .date { width: 170px; text-align: left; }
  .ledger .owner { text-align: center; }
  .presenter {
    position: absolute; left: 0; top: 1074px; width: 848px; text-align: center; font-size: 12px; line-height: 18px;
  }
  .presenter .company { font-family: "Josefin Sans", sans-serif; font-size: 12.5px; letter-spacing: 0.5px; }
</style>
</head>
<body>
<main class="poster">
  <div class="backdrop-trees" role="img" aria-label="Faded sepia silhouette of a large oak tree and a house behind it"></div>

  <svg class="frame" width="848" height="1200" viewBox="0 0 848 1200" aria-hidden="true">
    <g fill="none" stroke="var(--cream)">
      <rect x="30" y="30" width="788" height="1140" stroke-width="2"/>
      <rect x="40" y="40" width="768" height="1120" stroke-width="1.5"/>
      <rect x="318" y="72" width="212" height="32" rx="8" stroke-width="2"/>
      <rect x="165" y="158" width="518" height="176" rx="88" stroke-width="2.5"/>
      <rect x="177" y="168" width="494" height="156" rx="78" stroke-width="1.2"/>
      <line x1="318" y1="410" x2="530" y2="410" stroke-width="2.5"/>
    </g>
  </svg>

  <div class="ornament corner top-left" role="img" aria-label="Scrolling corner flourish"></div>
  <div class="ornament corner top-right" role="img" aria-label="Scrolling corner flourish"></div>
  <div class="ornament corner bottom-left" role="img" aria-label="Scrolling corner flourish"></div>
  <div class="ornament corner bottom-right" role="img" aria-label="Scrolling corner flourish"></div>
  <div class="ornament crest-top" role="img" aria-label="Filigree scrollwork above the title"></div>
  <div class="ornament crest-bottom" role="img" aria-label="Filigree scrollwork below the title"></div>

  <div class="label-tab">Tale of Dwelling</div>
  <h1 class="title">Wrenmarsh</h1>
  <div class="years">1835&nbsp;&nbsp;-&nbsp;2020</div>

  <section class="history">
    <p>Wrenmarsh is a neighborhood in the City of Pensacola. Located east of Cedar Bluff, Wrenmarsh is bordered by 9th Avenue to the west and 12th Avenue and Heron's Creek to the east. Initially developed in 1954, an addition was added in 1956. It is located in a beautiful area of America's 1st Settlement (1559), Pensacola, Florida encompassed with towering pine trees and breathtaking heritage oaks.</p>
    <p>The land comprising Wrenmarsh was originally owned by Mateo Arrabal under a Spanish Land Grant and affirmed by President Elias Thornbury on September 7, 1835. Spain relinquished Florida to the United States in 1819 under the Adams-Onis Treaty and lands previously granted to settlers prior thereto were honored if claims were filed and approved by the United States government.</p>
    <p>Through the years, the land changed hands many times but was eventually developed into the Wrenmarsh subdivision in 1954, by Walter Pennick, President of Wrenmarsh, Inc. The subdivision contains 63 lots with a beautiful, oak-filled park located just off of Larkspur Street. Built in 1957 and containing approximately 2606 square feet of living, garage and patio space, the home located at 417 Marigold Street is a trip back in time to when houses were carefully planned catering to modern sensibilities, neither too big nor too small, neither too formal nor too casual.</p>
  </section>

  <h2 class="ledger-heading">Tale of the Dwelling</h2>
  <table class="ledger">
    <tr><td class="date">September 9, 1835</td><td class="owner">Mateo Arrabal, Spanish Land Grant</td></tr>
    <tr><td class="date">April 27, 1954</td><td class="owner">Wrenmarsh Plat approved by Escambia County</td></tr>
    <tr><td class="date">April 29, 1957</td><td class="owner">Walter Pennick, III and Marian W. Pennick</td></tr>
    <tr><td class="date">September 20, 1960</td><td class="owner">Louisa Mae Harlow (Denby)</td></tr>
    <tr><td class="date">February 11, 1966</td><td class="owner">Henry T. Ashcombe and Ruth E. Ashcombe</td></tr>
    <tr><td class="date">January 20, 1995</td><td class="owner">Russell D. Caldwell</td></tr>
    <tr><td class="date">September 1, 2020</td><td class="owner">Russell D. Caldwell and Owen Marsh Tillery</td></tr>
  </table>

  <footer class="presenter">
    <div>Presented by</div>
    <div class="company">TALE OF DWELLING, LLC</div>
  </footer>
</main>
</body>
</html>
```